Vantiqo custom business card design

Need a authentic, innovative business card design for a new mobile app business. I am uploading a few screen images from our app for you to view. I would like app design theme to match business card design. I can also send logo images.

```html
<!DOCTYPE html>
<html lang="en">
<head>
<meta charset="utf-8">
<title>Vantiqo Business Card</title>
<link rel="stylesheet" href="https://fonts.googleapis.com/css2?family=Montserrat:wght@800&family=Work+Sans:wght@400;500&display=swap">
<style>
  :root {
    --brand-purple: #622a8c;
    --ink-black: #1f1f1f;
    --paper-white: #ffffff;
    --backdrop: #e9e4dc;
  }
  html, body {
    margin: 0;
    padding: 0;
    width: 1200px;
    height: 930px;
    overflow: hidden;
    background: var(--backdrop);
  }
  .stage {
    position: relative;
    width: 1200px;
    height: 930px;
  }
  .card {
    position: absolute;
    left: 318px;
    width: 564px;
    height: 323px;
    border-radius: 16px;
    overflow: hidden;
    background: var(--brand-purple);
    color: var(--paper-white);
    font-family: "Work Sans", sans-serif;
  }
  .card--front { top: 125px; }
  .card--back { top: 514px; }

  .card__art {
    position: absolute;
    inset: 0;
  }
  .brand-name {
    font-family: "Montserrat", sans-serif;
    font-weight: 800;
    letter-spacing: 0.5px;
    margin: 0;
    line-height: 1;
  }
  .card--front .brand-name {
    position: absolute;
    left: 21px;
    top: 27px;
    font-size: 44px;
  }
  .contact-block {
    position: absolute;
    left: 22px;
    top: 110px;
  }
  .person-name {
    margin: 0;
    font-size: 23px;
    font-weight: 500;
    letter-spacing: 0.6px;
    text-transform: uppercase;
    line-height: 1.1;
  }
  .person-role {
    margin: 2px 0 0;
    font-size: 16px;
  }
  .address {
    margin: 12px 0 0;
    font-style: normal;
    font-size: 16px;
    line-height: 21px;
    letter-spacing: 0.3px;
  }
  .contact-list {
    list-style: none;
    margin: 10px 0 0;
    padding: 0;
    font-size: 16px;
    line-height: 21px;
    letter-spacing: 0.3px;
  }
  .contact-list li {
    display: flex;
    align-items: center;
    gap: 9px;
  }
  .contact-list svg {
    width: 11px;
    height: 11px;
    flex: none;
  }
  .card--back .brand-mark {
    position: absolute;
    left: 210px;
    top: 64px;
    width: 144px;
    height: 144px;
    border-radius: 50%;
    background: var(--paper-white);
  }
  .card--back .brand-name {
    position: absolute;
    left: 0;
    right: 0;
    top: 217px;
    text-align: center;
    font-size: 44px;
  }
</style>
</head>
<body>
<main class="stage">

  <section class="card card--front" aria-label="Business card front">
    <svg class="card__art" width="564" height="323" viewBox="0 0 564 323" aria-hidden="true">
      <circle cx="420" cy="161" r="166" fill="var(--ink-black)"/>
      <rect x="426" y="0" width="138" height="323" fill="var(--paper-white)"/>
      <circle cx="428" cy="161" r="166" fill="var(--paper-white)"/>
      <circle cx="431" cy="161" r="96" fill="var(--brand-purple)"/>
    </svg>

    <h1 class="brand-name">Vantiqo</h1>

    <div class="contact-block">
      <p class="person-name">Daniel Carter</p>
      <p class="person-role">Director</p>
      <address class="address">1427 Harbor Lane<br>Coral Springs, FL 33065</address>
      <ul class="contact-list">
        <li>
          <svg viewBox="0 0 12 12"><rect x="3" y="1" width="6" height="10" rx="1" fill="none" stroke="currentColor" stroke-width="1.4"/><circle cx="6" cy="9" r="0.7" fill="currentColor"/></svg>
          (555) 204-1187
        </li>
        <li>
          <svg viewBox="0 0 12 12"><path d="M3 1.5 L5 1 L6 3.6 L4.8 4.6 Q5.6 6.8 7.4 7.6 L8.4 6.4 L11 7.4 L10.5 9.6 Q10 11 8.5 10.8 Q2.2 9.6 1.2 3.5 Q1 2 3 1.5 Z" fill="currentColor"/></svg>
          (555) 318-6402
        </li>
        <li>
          <svg viewBox="0 0 12 12"><rect x="1" y="2.5" width="10" height="7" rx="0.8" fill="none" stroke="currentColor" stroke-width="1.2"/><path d="M1.5 3 L6 6.5 L10.5 3" fill="none" stroke="currentColor" stroke-width="1.2"/></svg>
          info@Vantiqo.com
        </li>
        <li>
          <svg viewBox="0 0 12 12"><circle cx="6" cy="6" r="5" fill="none" stroke="currentColor" stroke-width="1.1"/><ellipse cx="6" cy="6" rx="2.2" ry="5" fill="none" stroke="currentColor" stroke-width="1"/><path d="M1 6 H11 M2 3.5 H10 M2 8.5 H10" stroke="currentColor" stroke-width="0.9"/></svg>
          www.Vantiqo.com
        </li>
      </ul>
    </div>
  </section>

  <section class="card card--back" aria-label="Business card back">
    <div class="brand-mark" aria-hidden="true"></div>
    <p class="brand-name">Vantiqo</p>
  </section>

</main>
</body>
</html>
```